Redesign of business card for Cedar Ridge Mechanical

We are looking for a new design for our business cards for Cedar Ridge Mechanical. We are a plumbing & HVAC construction company, operating on the West Coast of Canada and USA. Logo attached.
Industry/Entity Type
Construction - Plumbing & HVAC
Contact Information for Business Card
Name, address, phone numbers, email, website address
Look and feel
Each slider illustrates characteristics of the customer's brand and the style your logo design should communicate.

```html
<!DOCTYPE html>
<html lang="en">
<head>
<meta charset="utf-8">
<title>Cedar Ridge Mechanical – Business Card</title>
<link href="https://fonts.googleapis.com/css2?family=Oswald:wght@500&family=Open+Sans:wght@400;700&display=swap" rel="stylesheet">
<style>
  :root {
    --stage: #d6d6d6;
    --card-white: #ffffff;
    --card-black: #141414;
    --ink: #111111;
    --on-dark: #ffffff;
  }
  * { margin: 0; padding: 0; box-sizing: border-box; }
  html, body { width: 1200px; height: 896px; overflow: hidden; }
  body { background: var(--stage); position: relative; font-family: "Open Sans", Arial, sans-serif; }

  .card {
    position: absolute;
    left: 334px;
    width: 527px;
    height: 301px;
    border-radius: 24px;
    overflow: hidden;
    background: var(--card-white);
    box-shadow: 0 10px 24px rgba(0,0,0,0.18);
  }
  .card--front { top: 126px; }
  .card--back { top: 475px; background: var(--card-black); }

  .brand {
    position: absolute;
    display: flex;
    align-items: center;
    gap: 12px;
    font-family: "Oswald", "Arial Narrow", sans-serif;
    font-weight: 500;
    color: var(--ink);
    letter-spacing: 1px;
    line-height: 1;
    white-space: nowrap;
  }
  .brand__square { background: var(--ink); flex: none; }
  .card--front .brand { left: 50%; top: 50%; transform: translate(-50%, -50%); font-size: 30px; }
  .card--front .brand__square { width: 30px; height: 30px; }
  .card--back .brand { left: 22px; top: 139px; font-size: 17px; gap: 8px; }
  .card--back .brand__square { width: 18px; height: 18px; }

  .back-shape { position: absolute; inset: 0; }

  .contact { position: absolute; left: 336px; top: 54px; color: var(--on-dark); }
  .contact__name { font-weight: 700; font-size: 18px; letter-spacing: 0.3px; line-height: 1.2; }
  .contact__role { font-size: 13.5px; margin-left: 1px; }
  .contact__address { margin-top: 30px; font-size: 14px; line-height: 19px; }
  .contact__list { list-style: none; margin-top: 25px; font-size: 14px; line-height: 19px; }
  .contact__list li { display: flex; align-items: center; gap: 6px; }
  .contact__list svg { width: 12px; height: 12px; flex: none; }
</style>
</head>
<body>
  <section class="card card--front" aria-label="Card front">
    <div class="brand"><span class="brand__square"></span>CEDAR RIDGE MECHANICAL</div>
  </section>

  <section class="card card--back" aria-label="Card back">
    <svg class="back-shape" viewBox="0 0 527 301" aria-hidden="true">
      <circle cx="150" cy="151" r="155" fill="#ffffff"/>
      <circle cx="141" cy="151" r="157" fill="#141414"/>
      <circle cx="131" cy="151" r="153" fill="#ffffff"/>
    </svg>
    <div class="brand"><span class="brand__square"></span>CEDAR RIDGE MECHANICAL</div>

    <div class="contact">
      <p class="contact__name">DANIEL HAYES</p>
      <p class="contact__role">Managing Director</p>
      <p class="contact__address">Your address, City<br>State, Zip 1234</p>
      <ul class="contact__list">
        <li><svg viewBox="0 0 24 24"><path fill="#fff" d="M6.6 10.8a15.1 15.1 0 0 0 6.6 6.6l2.2-2.2a1 1 0 0 1 1-.25 11.4 11.4 0 0 0 3.6.57 1 1 0 0 1 1 1V20a1 1 0 0 1-1 1A17 17 0 0 1 3 4a1 1 0 0 1 1-1h3.5a1 1 0 0 1 1 1c0 1.25.2 2.45.57 3.57a1 1 0 0 1-.25 1z"/></svg>123 456 789</li>
        <li><svg viewBox="0 0 24 24"><path fill="#fff" d="M3 5h18v14H3zm2 2v.5l7 4.5 7-4.5V7zm0 2.9V17h14V9.9l-7 4.5z"/></svg>info@yourgmail.com</li>
        <li><svg viewBox="0 0 24 24"><circle cx="12" cy="12" r="9" fill="none" stroke="#fff" stroke-width="2.2"/><path fill="#fff" d="M8 6l3 2-1 3 3 2-1 4-3-3-2-4zM15 7l3 2v3l-3-1z"/></svg>www.yourwebsite.com</li>
      </ul>
    </div>
  </section>
</body>
</html>
```